The World Most Wanted Eyelahes

1. We need a web design for a new company based in California, USA
2. We are the manufacturer for 100% human hair eyelashes,
made in Indonesia.
3. We recently launched "Tapered Eyelashes" with human hair.
Currently, none of the people carried Tapered eyelash.
4. We would like to see designs that use the 4 different colors that match with my products as "Four Seasons" concepts.
5. We prefer to follow www.pelvo.com style, like professional website.
6. Focus on products as a manufacturer, therefore, all wholesaler and retailer copy and paste to their marketing tools.
7. Need bilingual English and Spanish.
8. Easy to link with social media.

Target Market(s)

United States and Central/South America.

Industry/Entity Type

Hair

Number of Pages Required

5+ page

Requirements
Must have
• 1. Details of Products with image.
• 2. Hottest/Newest Items "Tapered in 100% Human Hair"
• 3. Store Page
Nice to have
• 1. My competitors is Quorim Eyelash. http://www.quorimlashes.com/
• Please follow the concepts of it.
• 2. www.Pelvo.com: They have great products detail on the website.
• i would like to focus on "Tapered" for new styles of the eyelash.
• 3. I want to visitors can write down the "Reviews" in every single product.
• Please check the www.QTRCosmetics.com.
Should not have
• It's not salon/Shop for the beauty.
• No need an appointment.
• We are the manufacturer of the eyelash.

```html
<!DOCTYPE html>
<html lang="en">
<head>
<meta charset="utf-8">
<title>Lashvara Eyelashes</title>
<link href="https://fonts.googleapis.com/css2?family=Lato:wght@400;700&family=Open+Sans:wght@400;600&family=Pinyon+Script&display=swap" rel="stylesheet">
<style>
:root{
  --gold:#b8822f;
  --gold-dark:#9a6a22;
  --nav:#2c2c2c;
  --ink:#1e1e1e;
  --muted:#4a4a4a;
  --rose:#cf5f6c;
  --rose-btn:#a8323f;
  --magenta:#c12ea3;
  --magenta-btn:#85156f;
  --sun:#dcb82d;
  --sun-btn:#a88914;
  --sky:#8fbcd4;
  --sky-btn:#5b8aa3;
  --footer:#ececec;
}
*{box-sizing:border-box;margin:0;padding:0}
html,body{width:894px;height:1200px;overflow:hidden;background:#fff}
body{position:relative;font-family:'Lato',sans-serif;color:var(--ink)}
.topline{position:absolute;top:0;left:0;width:894px;height:2px;
  background:linear-gradient(90deg,var(--rose) 0 25%,var(--magenta) 25% 50%,var(--sun) 50% 75%,var(--sky) 75% 100%)}
.brand{position:absolute;left:74px;top:14px;width:122px;height:54px}
.brand .name{font-family:'Lato',sans-serif;font-size:24px;color:var(--gold);letter-spacing:1px;line-height:1}
.brand .sub{font-family:'Lato',sans-serif;font-size:10px;color:var(--gold);letter-spacing:3px;margin-top:4px}
.language{position:absolute;left:382px;top:32px;width:98px;height:22px;border:1px solid #bbb;font-size:7px;display:flex;align-items:center;justify-content:center;gap:4px}
.language .flag{width:9px;height:6px;background:linear-gradient(#b22 0 50%,#fff 50%);position:relative}
.language .flag::before{content:"";position:absolute;left:0;top:0;width:4px;height:3px;background:#2b3f8f}
.cart{position:absolute;top:14px;font-size:8.5px;display:flex;align-items:center;gap:6px}
.cart-a{left:637px}.cart-b{left:740px}
.cart-sep{position:absolute;left:722px;top:12px;width:1px;height:18px;background:#ccc}
.search{position:absolute;left:606px;top:46px;width:213px;height:24px;background:#f1f1f1}
.search .btn{position:absolute;right:0;top:0;width:27px;height:24px;background:#1e1e1e;display:flex;align-items:center;justify-content:center}
.nav{position:absolute;left:74px;top:82px;width:746px;height:30px;display:flex;background:linear-gradient(#3a3a3a,#1f1f1f)}
.nav a{color:#fff;text-decoration:none;font-size:10.5px;display:flex;align-items:center;justify-content:center;border-right:1px solid #444}
.nav a.active{background:linear-gradient(#c8953f,var(--gold-dark))}
.hero{position:absolute;left:74px;top:122px;width:746px;height:320px;
  background:radial-gradient(circle at 22% 55%,#d0307e 0,#7a2458 22%,#3a2a33 48%,#2c2c2c 70%)}
.hero-title{position:absolute;left:388px;top:108px;width:320px;font-family:'Pinyon Script',cursive;font-size:32px;line-height:44px;color:#fff}
.arrow{position:absolute;top:141px;width:22px;height:22px;border-radius:50%;background:rgba(255,255,255,.85);display:flex;align-items:center;justify-content:center}
.arrow.prev{left:14px}.arrow.next{right:14px}
.section-title{position:absolute;left:0;width:894px;text-align:center;font-family:'Open Sans',sans-serif;font-size:16px}
.welcome-title{top:457px}
.intro{position:absolute;left:84px;top:491px;width:726px;text-align:center;font-family:'Open Sans',sans-serif;font-size:9.2px;line-height:12.2px;color:var(--muted)}
.features{position:absolute;left:74px;top:568px;width:748px;display:flex;justify-content:space-between}
.feature{display:flex;gap:12px;font-size:9.5px;line-height:11px;width:140px}
.feature svg{flex:none}
.products-title{top:630px}
.cards{position:absolute;left:74px;top:668px;width:746px;display:flex;justify-content:space-between}
.card{width:176px;height:207px;padding:8px;text-align:center}
.card .photo{width:160px;height:139px;background:#fff}
.card h3{font-family:'Open Sans',sans-serif;font-weight:400;font-size:15px;color:#fff;margin-top:6px}
.card .more{display:inline-block;margin-top:3px;width:70px;height:16px;line-height:16px;font-size:10px;color:#fff;font-family:'Open Sans',sans-serif}
.card.spring{background:var(--rose)}.card.spring .more{background:var(--rose-btn)}
.card.summer{background:var(--magenta)}.card.summer .more{background:var(--magenta-btn)}
.card.autumn{background:var(--sun)}.card.autumn .more{background:var(--sun-btn)}
.card.winter{background:var(--sky)}.card.winter .more{background:var(--sky-btn)}
.photo.brush{background:linear-gradient(160deg,#f2f2f2,#9a8a80 55%,#e8dcd4)}
.photo.kit{background:radial-gradient(circle at 50% 50%,#c8486c,#f2f2f2 65%)}
.photo.set{background:linear-gradient(180deg,#fafafa 20%,#e8a0a8 65%,#d28a3a)}
.photo.tools{background:radial-gradient(circle at 50% 50%,#8a6a50,#fafafa 60%)}
.footer{position:absolute;left:0;top:920px;width:894px;height:280px;background:var(--footer)}
.col{position:absolute;top:32px}
.col h4{font-family:'Open Sans',sans-serif;font-weight:400;font-size:16px;color:#222;margin-bottom:14px}
.col li{list-style:none;font-family:'Open Sans',sans-serif;font-size:9px;color:#555;line-height:15.3px}
.newsletter{left:578px;width:242px}
.email{width:241px;height:45px;background:#fff;border:1px solid #ddd;display:flex;align-items:center;justify-content:center;font-size:9px;color:#333;margin-top:-2px}
.subscribe{width:241px;height:33px;background:#1e1e1e;color:#fff;font-family:'Open Sans',sans-serif;font-size:11.5px;display:flex;align-items:center;justify-content:center}
.newsletter h5{font-family:'Open Sans',sans-serif;font-weight:400;font-size:15px;margin:22px 0 6px}
.social{display:flex;gap:5px}
.social span{width:22px;height:22px;display:block}
.footer-rule{position:absolute;left:14px;top:240px;width:866px;height:1px;background:#dcdcdc}
.copyright{position:absolute;left:0;top:256px;width:884px;text-align:center;font-size:8.5px;color:#333}
</style>
</head>
<body>
<div class="topline"></div>

<header>
  <div class="brand"><div class="name">LASHVARA</div><div class="sub">EYELASHES</div></div>
  <div class="language"><span class="flag"></span>Language: English ▾</div>
  <div class="cart cart-a">Cart (Empty)
    <svg width="14" height="14" viewBox="0 0 14 14"><circle cx="7" cy="4" r="3.2" fill="#b8822f"/><path d="M1 14c0-4 3-6 6-6s6 2 6 6z" fill="#b8822f"/></svg></div>
  <div class="cart-sep"></div>
  <div class="cart cart-b">Cart (Empty)
    <svg width="18" height="14" viewBox="0 0 18 14"><path d="M1 1h3l2 8h9l2-6H5" fill="none" stroke="#b8822f" stroke-width="1.6"/><circle cx="7" cy="12" r="1.4" fill="#b8822f"/><circle cx="14" cy="12" r="1.4" fill="#b8822f"/></svg></div>
  <div class="search"><div class="btn"><svg width="12" height="12" viewBox="0 0 12 12"><circle cx="5" cy="5" r="3.8" fill="none" stroke="#fff" stroke-width="1.5"/><path d="M8 8l3 3" stroke="#fff" stroke-width="1.5"/></svg></div></div>
  <nav class="nav">
    <a class="active" style="width:118px">Home</a>
    <a style="width:110px">About Us</a>
    <a style="width:109px">Services</a>
    <a style="width:139px">Our Products</a>
    <a style="width:139px">Testimonials</a>
    <a style="width:131px;border-right:0">Contact Us</a>
  </nav>
</header>

<section class="hero" role="img" aria-label="Close-up of an eye wearing bold pink feathered lashes">
  <div class="hero-title">Tapered in 100% Human Hair</div>
  <div class="arrow prev"><svg width="10" height="10" viewBox="0 0 10 10"><path d="M6.5 1.5L3 5l3.5 3.5" fill="none" stroke="#333" stroke-width="1.6"/></svg></div>
  <div class="arrow next"><svg width="10" height="10" viewBox="0 0 10 10"><path d="M3.5 1.5L7 5 3.5 8.5" fill="none" stroke="#333" stroke-width="1.6"/></svg></div>
</section>

<h2 class="section-title welcome-title">Welcome To Our Site</h2>
<p class="intro">Lorem ipsum dolor sit amet, consectetur adipiscing elit. Aliquam sit amet fringilla est. Praesent nec condimentum lectus. Praesent tempus lacus massa, id tempor urna ele-mentum in. Etiam neque metus, faucibus ut sapien quis, mattis sodales nisi. Etiam non porttitor eros, sed varius quam. Duis semper neque tortor. Pellentesque in nisi varius, hendrerit justo id, laoreet sapien. Aliquam hendrerit urna sed enim tempus mattis. Cum sociis natoque penatibus et magnis dis parturient montes, nascetur ridiculus mus. Donec erat metus, fringilla a odio sed, posuere consectetur nisl. Pellentesque tincidunt eros odio, ac laoreet sapien rutrum iaculis.</p>

<ul class="features">
  <li class="feature"><svg width="12" height="12" viewBox="0 0 12 12"><circle cx="6" cy="6" r="6" fill="#222"/><path d="M3 6.2l2 2 4-4" fill="none" stroke="#fff" stroke-width="1.5"/></svg><span>New Technology WIth Tapered Hair</span></li>
  <li class="feature"><svg width="12" height="12" viewBox="0 0 12 12"><circle cx="6" cy="6" r="6" fill="#222"/><path d="M3 6.2l2 2 4-4" fill="none" stroke="#fff" stroke-width="1.5"/></svg><span>Brand New With Premium Packaging</span></li>
  <li class="feature"><svg width="12" height="12" viewBox="0 0 12 12"><circle cx="6" cy="6" r="6" fill="#222"/><path d="M3 6.2l2 2 4-4" fill="none" stroke="#fff" stroke-width="1.5"/></svg><span>Handmade WIth Premium Hair</span></li>
  <li class="feature"><svg width="12" height="12" viewBox="0 0 12 12"><circle cx="6" cy="6" r="6" fill="#222"/><path d="M3 6.2l2 2 4-4" fill="none" stroke="#fff" stroke-width="1.5"/></svg><span>Comportable With Natural And Soft</span></li>
  <li class="feature" style="width:120px"><svg width="12" height="12" viewBox="0 0 12 12"><circle cx="6" cy="6" r="6" fill="#222"/><path d="M3 6.2l2 2 4-4" fill="none" stroke="#fff" stroke-width="1.5"/></svg><span>You Look More Perfect With Lashvara</span></li>
</ul>

<h2 class="section-title products-title">Our Products</h2>
<div class="cards">
  <article class="card spring"><div class="photo brush" role="img" aria-label="Makeup brush with loose powder"></div><h3>Blosssom Eye’s</h3><span class="more">More</span></article>
  <article class="card summer"><div class="photo kit" role="img" aria-label="Assorted cosmetics arranged in a circle"></div><h3>Blosssom Eye’s</h3><span class="more">More</span></article>
  <article class="card autumn"><div class="photo set" role="img" aria-label="Collection of brushes, polish and palettes"></div><h3>Blosssom Eye’s</h3><span class="more">More</span></article>
  <article class="card winter"><div class="photo tools" role="img" aria-label="Scattered makeup tools and products"></div><h3>Blosssom Eye’s</h3><span class="more">More</span></article>
</div>

<footer class="footer">
  <div class="col" style="left:73px"><h4>Shopping with us</h4><ul>
    <li>Why shop with us?</li><li>How it works</li><li>Delivery</li><li>Returns</li><li>Where's my order</li><li>Contact &amp; help</li><li>Wedding list</li><li>Wish lists</li><li>Gift vouchers</li></ul></div>
  <div class="col" style="left:251px;top:35px"><h4>About us</h4><ul>
    <li>Our story</li><li>Customer contact</li><li>Awards</li><li>Press centre</li><li>Work with us</li><li>Terms &amp; conditions</li><li>Privacy &amp; cookies</li></ul></div>
  <div class="col" style="left:402px;top:35px"><h4>Selling with us</h4><ul>
    <li>Why join?</li><li>FAQ's</li><li>Apply to sell with us</li><li>Affiliates</li></ul></div>
  <div class="col newsletter" style="top:36px"><h4>Signup newsletter</h4>
    <div class="email">EMAIL ID</div>
    <div class="subscribe">SUBSCRIBE NOW</div>
    <h5>Keep in touch</h5>
    <div class="social">
      <span style="background:#f0a020" aria-label="Feed"></span>
      <span style="background:#2d4a8a" aria-label="Social link"></span>
      <span style="background:#3a9ad9" aria-label="Social link"></span>
      <span style="background:#fff" aria-label="Social link"></span>
      <span style="background:#3a6fb0" aria-label="Social link"></span>
    </div>
  </div>
  <div class="footer-rule"></div>
  <div class="copyright">Copyright © 2015yoursite,&nbsp; All right reserved</div>
</footer>
</body>
</html>
```